UL Aesthetic improvement on full website

brightneighbourhq.com
We need someone to improve the current website brightneighbourhq.com
Some designed to fail to follow isntruction and deliver. please find attached summary latest design requirement, please follow and read each of the requirements carefully and submit max two versions only. The winner would have to deliver within 5 days

Sample reference : velmorq.com/html/brightneighbour/#
(previous winner cant deliver)
*All of our wording and graphic content are updated, designer wouldn't involve in recreating any content.
Designer may use template or own material. delivery in html and implement on our WordPress server

please submit about us the project submission.
upon the winning, you have to maintain sub content / pages and submit the full site with your improved version of full websites including inner pages

Low design quality

Target Market(s)

general audience

Industry/Entity Type

social service

Number of Pages Required

5+ page

Requirements
Must have
• feeling and look similar to pobrix dot com
Nice to have
• extend the same style to other pages

```html
<!DOCTYPE html>
<html lang="en">
<head>
<meta charset="utf-8">
<title>Bright Neighbour — New Way of Giving</title>
<link href="https://fonts.googleapis.com/css2?family=Poppins:wght@300;400;500;600;700;800&family=Patrick+Hand&display=swap" rel="stylesheet">
<style>
:root{
  --coral:#f8696b;
  --coral-soft:#ff8a8a;
  --blush:#fde4e6;
  --lavender:#f6f6fb;
  --ink:#1c1c1c;
  --muted:#6f6f6f;
  --white:#ffffff;
  --yellow:#f6b82d;
  --navy:#2a2f86;
  --green:#21b07a;
}
*{box-sizing:border-box;margin:0;padding:0}
html,body{width:1200px;height:4118px;overflow:hidden}
body{position:relative;font-family:"Poppins",sans-serif;color:var(--ink);background:var(--white)}
.btn{position:absolute;display:flex;align-items:center;justify-content:center;border-radius:30px;background:var(--coral);color:var(--white);font-weight:600;font-size:14px;letter-spacing:1px;text-transform:uppercase;white-space:nowrap}
.accent{color:var(--coral)}

/* hero */
.hero{position:absolute;left:0;top:0;width:1200px;height:711px;background:linear-gradient(180deg,#fff 0%,#fff 45%,#fde3e6 100%);overflow:hidden}
.brand-mark{position:absolute;left:61px;top:13px;width:64px;height:64px;border-radius:50%;background:var(--coral);color:#fff;font-size:7.5px;font-weight:600;letter-spacing:.6px;display:flex;align-items:center;justify-content:center;text-align:center;line-height:1.3;white-space:nowrap}
.nav{position:absolute;top:34px;right:72px;display:flex;gap:22px;font-size:12.5px;align-items:center}
.nav a{color:var(--ink);text-decoration:none;position:relative}
.nav .current::before{content:"";position:absolute;left:-12px;top:-5px;width:30px;height:30px;border-radius:50%;background:var(--coral);z-index:-1}
.nav .user{width:22px;height:22px}
.tagline-art{position:absolute;left:0;top:88px;width:260px;height:160px;border-radius:60px;background:linear-gradient(135deg,#f6b82d 0%,#ffe9ea 60%,#fff 100%);opacity:.8}
.hero-kicker{position:absolute;left:115px;top:262px;font-family:"Patrick Hand",cursive;font-size:36px;color:var(--ink)}
.hero-title{position:absolute;left:113px;top:305px;font-weight:800;font-size:60px;line-height:64px;letter-spacing:1px}
.hero-sub{position:absolute;left:116px;top:442px;font-size:14px}
.hero-circle{position:absolute;left:615px;top:113px;width:512px;height:512px;border-radius:50%;background:#fff;box-shadow:0 0 0 2px var(--coral)}
.hero-circle-text{position:absolute;left:0;top:90px;width:100%;text-align:center;font-size:22px;font-weight:500;line-height:30px}
.circle-art{position:absolute;left:40px;top:180px;width:420px;height:150px;border-radius:20px;background:linear-gradient(90deg,#eee 0%,#f7f7f7 60%,#ffd2da 100%)}
.crowd-art{position:absolute;left:460px;top:440px;width:740px;height:271px;border-radius:180px 180px 0 0;background:linear-gradient(90deg,#f8696b 0%,#21b07a 35%,#f6b82d 60%,#2a2f86 80%,#f6b82d 100%);opacity:.92}

/* hello */
.hello-phones{position:absolute;left:192px;top:794px;width:360px;height:353px;border-radius:28px;background:linear-gradient(135deg,#ffe0e3 0%,#fff6f6 50%,#ffd9dc 100%)}
.hello-title{position:absolute;left:662px;top:790px;font-size:33px;font-weight:600;line-height:40px;white-space:nowrap}
.hello-copy{position:absolute;left:662px;top:878px;width:380px;font-size:11.5px;line-height:19.5px;color:var(--muted)}
.hello-copy p{margin-bottom:10px}
.hello-copy b{color:var(--coral);font-weight:600}

/* unique */
.unique{position:absolute;left:0;top:1262px;width:1200px;height:620px;background:var(--lavender)}
.section-title{position:absolute;left:0;width:1200px;text-align:center;font-size:32px;font-weight:600;line-height:42px}
.card{position:absolute;top:1413px;width:215px;height:287px;background:#fff;border-radius:6px;box-shadow:0 4px 18px rgba(0,0,0,.05);text-align:center;padding:0 26px}
.card svg{display:block;margin:30px auto 0}
.card h3{margin:22px -14px 0;font-size:15px;font-weight:600;white-space:nowrap}
.card p{margin-top:14px;font-size:12px;line-height:19.5px;color:var(--muted)}
.side-art-right{position:absolute;left:1060px;top:1450px;width:140px;height:320px;border-radius:70px 0 0 70px;background:linear-gradient(180deg,#f8696b 0%,#f8696b 60%,#2a2f86 100%)}

/* video */
.blob{position:absolute;left:219px;top:1960px;width:762px;height:415px}
.video-frame{position:absolute;left:331px;top:1798px;width:538px;height:295px;background:#fff;border:3px solid var(--ink)}
.video-art{position:absolute;left:20px;top:44px;width:492px;height:220px;background:linear-gradient(180deg,#f4f4f4,#e8e8e8)}
.video-label{position:absolute;left:0;top:12px;width:100%;text-align:center;font-family:"Patrick Hand",cursive;font-size:20px}
.play{position:absolute;left:232px;top:130px;width:56px;height:38px;border-radius:10px;background:#e02d1f}
.play::after{content:"";position:absolute;left:22px;top:11px;border-left:14px solid #fff;border-top:8px solid transparent;border-bottom:8px solid transparent}
.video-tag{position:absolute;left:0;width:1200px;text-align:center;color:#fff}
.side-art-left{position:absolute;left:0;top:1975px;width:240px;height:250px;border-radius:0 120px 120px 0;background:linear-gradient(135deg,#f6b82d 0%,#2a2f86 70%)}

/* how it works */
.step{position:absolute;left:231px;display:flex;align-items:center}
.step-num{width:44px;height:44px;border-radius:50%;background:#fde9ea;display:flex;align-items:center;justify-content:center;font-size:20px;font-weight:600;color:var(--ink)}
.step-num.first{color:#f5a2a4}
.step-name{margin-left:19px;font-size:18px;font-weight:500}
.step-line{position:absolute;left:253px;top:2640px;width:1px;height:135px;background:var(--coral);opacity:.5}
.step-copy{position:absolute;left:296px;top:2640px;width:360px;font-size:11.5px;line-height:19.5px;color:var(--muted)}
.step-copy p{margin-bottom:20px}
.app-phone{position:absolute;left:773px;top:2570px;width:232px;height:460px;border-radius:26px;border:7px solid #1d2a4a;background:linear-gradient(180deg,#ffd4d6 0%,#fff 35%,#fff 60%,#e9c4c8 100%)}

/* banner */
.banner{position:absolute;left:142px;top:3108px;width:915px;height:336px;border-radius:60px;background:var(--coral);overflow:hidden}
.banner::before{content:"";position:absolute;inset:12px;border:1px solid rgba(255,255,255,.45);border-radius:50px}
.banner-art{position:absolute;left:0;top:30px;width:440px;height:306px;border-radius:120px 120px 0 0;background:linear-gradient(90deg,#f6b82d 0%,#2a2f86 45%,#21b07a 85%)}
.banner-title{position:absolute;left:440px;top:86px;width:475px;text-align:center;font-size:38px;font-weight:600;letter-spacing:.5px}
.banner-sub{position:absolute;left:440px;top:140px;width:475px;text-align:center;font-size:23px;font-weight:500;color:#fff}
.banner-note{position:absolute;left:440px;top:182px;width:475px;text-align:center;font-size:13.5px;color:#2a2a2a}
.btn.outline{background:transparent;border:1.5px solid #fff;color:#fff;font-size:13px}

/* partners */
.partners{position:absolute;left:0;top:3590px;width:1200px;height:56px}
.partner{position:absolute;top:12px;height:32px;display:flex;align-items:center;justify-content:center;font-weight:600;font-size:18px;white-space:nowrap}
.arrow{position:absolute;top:3600px;width:16px;height:28px}

/* footer */
.footer{position:absolute;left:0;top:3710px;width:1200px;height:408px;background:linear-gradient(180deg,#fde5e7 0%,#fff2f3 100%)}
.f-logo{position:absolute;left:141px;top:50px;width:128px;height:128px;border-radius:50%;background:var(--coral);color:#fff;font-size:14px;font-weight:500;letter-spacing:1.5px;line-height:22px;display:flex;align-items:center;justify-content:center;text-align:center;white-space:nowrap}
.f-about{position:absolute;left:60px;top:198px;width:290px;text-align:center;font-size:11.5px;line-height:19px}
.f-social{position:absolute;left:113px;top:251px;display:flex;gap:6px}
.f-social span{width:36px;height:36px;border-radius:50%;background:var(--coral);display:flex;align-items:center;justify-content:center}
.f-head{position:absolute;top:46px;font-size:18px;font-weight:600;white-space:nowrap}
.f-links{position:absolute;left:397px;top:87px;list-style:none;font-size:11.5px;line-height:22.4px}
.f-news-copy{position:absolute;left:672px;top:86px;width:430px;font-size:11.5px;line-height:22px}
.field{position:absolute;left:672px;width:411px;height:36px;border-radius:18px;background:#fff;border:1px solid #f3cfd2;font-size:11.5px;color:#9a9a9a;padding-left:18px;display:flex;align-items:center}
.f-check{position:absolute;left:672px;top:242px;display:flex;align-items:center;gap:10px;font-size:12px}
.f-check i{width:12px;height:12px;border:1px solid var(--coral);display:block}
.f-rule{position:absolute;left:60px;top:358px;width:1080px;height:1px;background:#f2c9cc}
.f-copy{position:absolute;left:0;top:374px;width:1200px;text-align:center;font-size:11px;color:#444}
</style>
</head>
<body>

<header class="hero">
  <div class="tagline-art" role="img" aria-label="Illustrated person waving beside a speech bubble reading Making Someone Smile Today"></div>
  <div class="brand-mark">BRIGHT<br>NEIGHBOUR</div>
  <nav class="nav">
    <a class="current">Home</a><a>About Us</a><a>Our Story</a><a>Social Impact</a><a>Join Us</a>
    <svg class="user" viewBox="0 0 22 22"><circle cx="11" cy="11" r="9.5" fill="none" stroke="#1c1c1c" stroke-width="1.6"/><circle cx="11" cy="9" r="3.2" fill="none" stroke="#1c1c1c" stroke-width="1.6"/><path d="M5 17c2-3 10-3 12 0" fill="none" stroke="#1c1c1c" stroke-width="1.6"/></svg>
  </nav>
  <div class="hero-kicker">new way of giving</div>
  <h1 class="hero-title">SOCIAL<br><span class="accent">INCLUSION</span></h1>
  <p class="hero-sub">In a World Where you Can be Anything, Be Kind.</p>
  <div class="btn" style="left:115px;top:477px;width:184px;height:38px">Pay-it-forward</div>
  <div class="hero-circle">
    <div class="hero-circle-text">Gain Back Their Self-Reliance<br>During A <span class="accent">Difficult Time</span></div>
    <div class="circle-art" role="img" aria-label="Line drawing of a community group crossing a bridge towards a smiling heart"></div>
  </div>
  <div class="crowd-art" role="img" aria-label="Colourful illustrated crowd of people reaching upward together"></div>
</header>

<section>
  <div class="hello-phones" role="img" aria-label="Three phone screens showing the giving app with merchants and meal listings"></div>
  <h2 class="hello-title">Hello,<br><span class="accent">Bright Neighbours!</span></h2>
  <div class="hello-copy">
    <p>Just like you, we resonate with a variety of social causes. At the core of everything, we believe that many societal challenges could be minimized merely by being more kind to one another and showing more trust in each other, especially during these difficult times.</p>
    <p>Therefore, we digitalised the traditional concept of <b>“Paying-it-forward”</b> to cultivate the new normal with timely help to include everyone. We strengthens the invisible community before it’s too late.</p>
    <p>The primary goal is to create a social movement where everyone demonstrates graciousness and kind understanding for the invisible struggles.</p>
  </div>
  <div class="btn" style="left:662px;top:1148px;width:144px;height:38px">Know more</div>
</section>

<section class="unique"></section>
<h2 class="section-title" style="top:1334px">What Makes <span class="accent">Us Unique</span></h2>
<div class="card" style="left:142px">
  <svg width="46" height="72" viewBox="0 0 46 72"><rect x="3" y="2" width="40" height="68" rx="5" fill="#3b3b3b"/><rect x="7" y="10" width="32" height="50" fill="#e9e9e9"/><rect x="13" y="28" width="20" height="14" fill="var(--coral)"/><circle cx="31" cy="27" r="4" fill="#3b3b3b"/></svg>
  <h3>Transparency</h3>
  <p>Witnessing every positive impact as a new way of giving.</p>
</div>
<div class="card" style="left:376px">
  <svg width="60" height="72" viewBox="0 0 60 72"><path d="M14 4l3 8M26 2v9M38 4l-3 8" stroke="var(--coral)" stroke-width="4" stroke-linecap="round"/><path d="M20 20c4-3 8 0 8 4v14l14-2c6 0 8 6 4 10L30 66c-8 4-20-2-20-14V30c0-4 4-6 10-10z" fill="#c9c9cc"/></svg>
  <h3>Easy &amp; Affordable</h3>
  <p>Be part of the Kind ripple effect with an accessible way.</p>
</div>
<div class="card" style="left:609px">
  <svg width="90" height="72" viewBox="0 0 90 72"><path d="M62 44C48 34 44 26 48 18c3-7 12-7 14 0 2-7 11-7 14 0 4 8 0 16-14 26z" fill="var(--coral)"/><path d="M4 42h20l14 8h16c4 0 4 6 0 6H34" fill="none" stroke="#bdbdc2" stroke-width="5" stroke-linecap="round"/><rect x="2" y="38" width="10" height="18" fill="#bdbdc2"/></svg>
  <h3>Personalised Kindness</h3>
  <p>Sending a personalised encouragement note as a piece of priceless kindness.</p>
</div>
<div class="card" style="left:843px">
  <svg width="60" height="72" viewBox="0 0 60 72"><rect x="6" y="2" width="42" height="68" rx="4" fill="#d6d6da"/><rect x="18" y="8" width="18" height="3" fill="#fff"/><circle cx="27" cy="32" r="6" fill="#fff"/><path d="M16 56c0-10 22-10 22 0z" fill="#fff"/><path d="M50 24c-6-4-7-8-5-10s4-1 5 1c1-2 3-3 5-1s1 6-5 10z" fill="var(--coral)"/><path d="M50 44c-6-4-7-8-5-10s4-1 5 1c1-2 3-3 5-1s1 6-5 10z" fill="var(--coral)"/></svg>
  <h3>Live</h3>
  <p>Directing your contributions to make immediate availability possible to those who needs it the most.</p>
</div>
<div class="side-art-right" role="img" aria-label="Illustrated person leaning in from the right edge"></div>

<svg class="blob" viewBox="0 0 762 415" aria-hidden="true"><path d="M140 20C260 -10 480 40 620 20c120-18 150 80 130 170-20 90-120 110-220 160-120 60-260 80-380 20C40 320-10 230 20 150 45 80 60 40 140 20z" fill="var(--coral)"/></svg>
<div class="side-art-left" role="img" aria-label="Illustrated woman reaching out towards the video"></div>
<div class="video-frame">
  <div class="video-label">Social Inclusion</div>
  <div class="video-art" role="img" aria-label="Line drawing of a diverse group of community members, including a wheelchair user and an elderly person"></div>
  <div class="play"></div>
</div>
<div class="video-tag" style="top:2128px;font-size:31px;font-weight:600">If You Can't Pay Back</div>
<div class="video-tag" style="top:2173px;font-size:46px;font-weight:700">Timely Help</div>
<div class="btn outline" style="left:508px;top:2245px;width:182px;height:38px">Pay-it-forward</div>

<h2 class="section-title" style="top:2455px;font-weight:500">How Bright Neighbours<br><span class="accent">Work</span></h2>
<div class="step-line"></div>
<div class="step" style="top:2594px"><span class="step-num first">1</span><span class="step-name">Contributors</span></div>
<div class="step-copy">
  <p>You can Pay-it-forward products and services listings on our platform just like any other e-commerce platform with Kind Messages.</p>
  <p>The platform will match with beneficiary who require the contributions with the personalized kind message. Contributor will receive an alert once the beneficiary claims their contributions.</p>
</div>
<div class="step" style="top:2826px"><span class="step-num">2</span><span class="step-name">Merchants</span></div>
<div class="step" style="top:2896px"><span class="step-num">3</span><span class="step-name">Community Partners</span></div>
<div class="step" style="top:2961px"><span class="step-num">4</span><span class="step-name">Beneficiaries</span></div>
<div class="app-phone" role="img" aria-label="Phone screen of the app showing food categories and featured merchants"></div>

<section class="banner">
  <div class="banner-art" role="img" aria-label="Illustration of three cheerful friends posing together"></div>
  <h2 class="banner-title">SOCIAL INCLUSION</h2>
  <p class="banner-sub">Ensure No One Is Left Out</p>
  <p class="banner-note">Make a Positive contribution to Society.</p>
  <div class="btn outline" style="left:563px;top:214px;width:165px;height:38px">Social Impact</div>
</section>

<h2 class="section-title" style="top:3514px">Partners</h2>
<svg class="arrow" style="left:61px" viewBox="0 0 16 28"><path d="M14 2L3 14l11 12" fill="none" stroke="#1c1c1c" stroke-width="2"/></svg>
<svg class="arrow" style="left:1125px" viewBox="0 0 16 28"><path d="M2 2l11 12L2 26" fill="none" stroke="#1c1c1c" stroke-width="2"/></svg>
<div class="partners">
  <div class="partner" style="left:130px;width:180px;color:#1f2a6b">Harbourline Poly</div>
  <div class="partner" style="left:340px;width:90px;color:#1aa84c">Rydo</div>
  <div class="partner" style="left:460px;width:180px;color:#8b1d3b">Civitek Authority</div>
  <div class="partner" style="left:660px;width:120px;color:#c8501f">Lumen Hub</div>
  <div class="partner" style="left:795px;width:130px;color:#1f2a6b">Eastvale Uni</div>
  <div class="partner" style="left:945px;width:120px;color:#1c1c1c">Meribank</div>
</div>

<footer class="footer">
  <div class="f-logo">BRIGHT<br>NEIGHBOUR</div>
  <p class="f-about">A Singapore Social Enterprise.In a world where you can be anything, be kind.</p>
  <div class="f-social">
    <span></span><span></span><span></span>
    <span><svg width="16" height="12" viewBox="0 0 16 12"><rect x="1" y="1" width="14" height="10" rx="1" fill="none" stroke="#fff" stroke-width="1.4"/><path d="M1 1l7 6 7-6" fill="none" stroke="#fff" stroke-width="1.4"/></svg></span>
  </div>
  <h3 class="f-head" style="left:397px">Site<span class="accent">Map</span></h3>
  <ul class="f-links">
    <li>Home</li><li>About Us</li><li>Our Story</li><li>Social Impact</li><li>Bright Neighbour</li><li>Bright Business</li><li>Merchant</li><li>The Bright Gift</li><li>FAQs</li><li>Contact Us</li>
  </ul>
  <h3 class="f-head" style="left:672px">Subscribe To Our <span class="accent">Newsletter</span></h3>
  <p class="f-news-copy">Let’s stay in touch! We would like to keep you inspired with our Kindness stories and community events.</p>
  <div class="field" style="top:141px">First Name</div>
  <div class="field" style="top:189px">Email</div>
  <div class="f-check"><i></i>By continuing, you accept the privacy policy</div>
  <div class="btn" style="left:672px;top:272px;width:133px;height:36px;font-size:13px">Subscribe</div>
  <div class="f-rule"></div>
  <p class="f-copy">©<span class="accent">BRIGHT NEIGHBOUR</span> - 2021 All rights reserved.</p>
</footer>

</body>
</html>
```